design a construction company business card

Design business card around our logo. Card must have all the typical info: name, title, address, phone, email, business name, etc. Somewhere on the card I would like to see our motto "Built on integrity... Inspired by commitment." Consider adding a splash of bright orange to the card to complement the blues and silvers/grays in the logo. We are open to metallic inks, textures, etc. We would like to see options on both light and dark backgrounds. The font in the logo is Euro Technic Extended Regular.

```html
<!DOCTYPE html>
<html lang="en">
<head>
<meta charset="utf-8">
<title>Halden Builders, Inc. — Business Card</title>
<link rel="stylesheet" href="https://fonts.googleapis.com/css2?family=Roboto:ital,wght@0,300;0,400;0,500;0,700;1,400&display=swap">
<style>
  :root {
    --backdrop: #2b2b2d;
    --card-dark: #1f1f21;
    --silver: #c4c4c6;
    --motto-grey: #9a9a9c;
    --paper: #e9e9ea;
    --brand-blue: #1f33a0;
    --blue-deep: #1a2a8c;
    --blue-light: #2240b8;
    --ink-light: #f2f4fb;
  }
  * { margin: 0; padding: 0; box-sizing: border-box; }
  html, body {
    width: 1070px; height: 1200px; overflow: hidden;
    background: var(--backdrop);
    font-family: "Roboto", Arial, sans-serif;
  }
  .canvas { position: relative; width: 1070px; height: 1200px; }

  .card-front {
    position: absolute; left: 155px; top: 115px;
    width: 775px; height: 425px;
    background: var(--card-dark);
  }
  .front-name {
    position: absolute; left: 0; right: 0; top: 300px;
    text-align: center;
    font-size: 40px; font-weight: 500; letter-spacing: 6px;
    color: var(--silver); text-transform: uppercase;
  }
  .front-mark {
    position: absolute; left: 368px; top: 230px;
    width: 40px; height: 40px; background: var(--silver);
  }
  .motto {
    position: absolute; left: 0; right: 0; top: 306px;
    text-align: center;
    font-size: 18px; font-style: italic; color: var(--motto-grey);
  }
  .motto { top: 306px; }

  .card-back {
    position: absolute; left: 150px; top: 628px;
    width: 782px; height: 432px;
    display: flex;
  }
  .back-brand {
    width: 412px; height: 100%;
    background: var(--paper);
    display: flex; align-items: center; justify-content: center; gap: 14px;
  }
  .brand-square { width: 22px; height: 22px; background: var(--brand-blue); }
  .brand-name {
    font-size: 30px; font-weight: 700; line-height: 1.15;
    color: var(--brand-blue); text-transform: uppercase; letter-spacing: 1px;
  }
  .back-contact {
    flex: 1; height: 100%;
    background: linear-gradient(160deg, var(--blue-light), var(--blue-deep));
    color: var(--ink-light);
    padding: 100px 0 0 64px;
  }
  .person-name { font-size: 25px; font-weight: 500; letter-spacing: 3px; }
  .person-title { font-size: 18px; font-weight: 500; margin-top: 4px; }
  .address { font-size: 17px; font-weight: 300; line-height: 22px; margin-top: 42px; }
  .contact-list { list-style: none; margin-top: 14px; }
  .contact-list li {
    display: flex; align-items: center; gap: 10px;
    font-size: 17px; font-weight: 300; line-height: 23.5px;
  }
  .contact-list svg { width: 17px; height: 17px; fill: var(--ink-light); }
</style>
</head>
<body>
<div class="canvas">
  <section class="card-front">
    <div class="front-name" style="top:200px">Halden Builders</div>
    <p class="motto">Built on integrity... Inspired by commitment.</p>
  </section>

  <section class="card-back">
    <div class="back-brand">
      <span class="brand-square"></span>
      <span class="brand-name">Halden<br>Builders, Inc.</span>
    </div>
    <div class="back-contact">
      <p class="person-name">MARCUS REED</p>
      <p class="person-title">CEO/Founder</p>
      <p class="address">4120 Cedar Ridge Road<br>Boise, Idaho 83702</p>
      <ul class="contact-list">
        <li><svg viewBox="0 0 24 24"><path d="M6.6 10.8c1.4 2.8 3.8 5.1 6.6 6.6l2.2-2.2c.3-.3.7-.4 1-.2 1.1.4 2.3.6 3.6.6.6 0 1 .4 1 1V20c0 .6-.4 1-1 1C10.6 21 3 13.4 3 4c0-.6.4-1 1-1h3.5c.6 0 1 .4 1 1 0 1.3.2 2.5.6 3.6.1.3 0 .7-.2 1z"/></svg>208 555 0147</li>
        <li><svg viewBox="0 0 24 24"><path d="M3 6h18v12H3z" fill="none"/><path d="M2 5h20v14H2V5zm2 2v.5l8 5 8-5V7H4zm0 3v7h16v-7l-8 5-8-5z"/></svg>office@haldenbuild.com</li>
        <li><svg viewBox="0 0 24 24"><path d="M12 2a10 10 0 100 20 10 10 0 000-20zm6.9 6h-2.9a15 15 0 00-1.4-3.6A8 8 0 0118.9 8zM12 4c.8 1.2 1.5 2.5 1.9 4h-3.8c.4-1.5 1.1-2.8 1.9-4zM4.3 14a8 8 0 010-4h3.4a16 16 0 000 4H4.3zm.8 2h2.9c.3 1.3.8 2.5 1.4 3.6A8 8 0 015.1 16zM8 8H5.1a8 8 0 014.3-3.6C8.8 5.5 8.3 6.7 8 8zm4 12c-.8-1.2-1.5-2.5-1.9-4h3.8c-.4 1.5-1.1 2.8-1.9 4zm2.3-6H9.7a14 14 0 010-4h4.6a14 14 0 010 4zm.3 5.6c.6-1.1 1.1-2.3 1.4-3.6h2.9a8 8 0 01-4.3 3.6zm1.7-5.6a16 16 0 000-4h3.4a8 8 0 010 4h-3.4z"/></svg>www.haldenbuild.com</li>
      </ul>
    </div>
  </section>
</div>
</body>
</html>
```